MRT Property - Business Cards

Looking for a business card & general letterhead, signage etc design for our new logo.

Colours:
000a20
0056a2
00b5ef
0088ce
68cef2

Fonts:
Poppins
Karla

Please keep look and feel of new brand - example in the zip package I sent.

```html
<!DOCTYPE html>
<html lang="en">
<head>
<meta charset="utf-8">
<title>MRT Property – Business Cards</title>
<link rel="stylesheet" href="https://fonts.googleapis.com/css2?family=Poppins:wght@700&family=Montserrat:wght@400;500&family=Caveat:wght@500&display=swap">
<style>
  :root {
    --navy: #000a20;
    --card-back: #12162a;
    --brand-blue: #0056a2;
    --sky: #00b5ef;
    --mid-blue: #0088ce;
    --light-blue: #68cef2;
    --ink: #1d1d1f;
    --page: #9b9b9b;
    --white: #ffffff;
  }
  * { box-sizing: border-box; margin: 0; padding: 0; }
  html, body { width: 1093px; height: 1200px; overflow: hidden; }
  body {
    background: var(--page);
    position: relative;
    font-family: "Montserrat", sans-serif;
  }
  .card {
    position: absolute;
    left: 265px;
    width: 580px;
    height: 363px;
    border-radius: 22px;
    overflow: hidden;
  }
  .card--front { top: 225px; background: var(--white); }
  .card--back  { top: 616px; background: var(--card-back); }

  .front-artwork {
    position: absolute;
    left: 0; top: 0;
    width: 290px; height: 100%;
    background: linear-gradient(100deg, var(--light-blue) 0%, var(--mid-blue) 45%, rgba(0,136,206,0.35) 75%, rgba(255,255,255,0) 100%);
  }
  .front-details {
    position: absolute;
    left: 298px; top: 30px;
    width: 260px;
  }
  .brand-name {
    font-family: "Poppins", sans-serif;
    font-weight: 700;
    font-size: 34px;
    line-height: 1;
    color: var(--brand-blue);
    white-space: nowrap;
  }
  .brand-name--front { margin-top: 30px; }
  .person-name {
    margin-top: 50px;
    margin-left: 5px;
    font-family: "Caveat", cursive;
    font-weight: 500;
    font-size: 31px;
    line-height: 1;
    color: var(--brand-blue);
  }
  .person-role {
    margin-left: 7px;
    margin-top: 2px;
    font-size: 13px;
    color: var(--ink);
  }
  .address {
    margin-left: 7px;
    margin-top: 22px;
    font-size: 14px;
    line-height: 16px;
    color: var(--ink);
  }
  .contact-list { list-style: none; margin-top: 22px; margin-left: 7px; }
  .contact-list li {
    display: flex; align-items: center; gap: 8px;
    height: 25px;
    font-size: 13.5px;
    color: var(--ink);
  }
  .contact-list svg { width: 13px; height: 13px; flex: none; fill: var(--mid-blue); }

  .back-pattern {
    position: absolute; inset: 0;
    background: radial-gradient(ellipse at 0% 0%, rgba(64,88,170,0.9) 0%, rgba(40,50,100,0.55) 30%, rgba(18,22,42,0) 60%), var(--card-back);
  }
  .brand-name--back {
    position: absolute;
    left: 352px; top: 278px;
    font-size: 26px;
    color: var(--white);
  }
</style>
</head>
<body>
  <section class="card card--front" aria-label="Business card front">
    <div class="front-artwork" role="img" aria-label="Large blue brand symbol decoration"></div>
    <div class="front-details">
      <p class="brand-name brand-name--front">MRT Property</p>
      <p class="person-name">Dana Wells</p>
      <p class="person-role">Managing Director</p>
      <p class="address">48 Cedar Hollow Road<br>Fairview, TN 37062</p>
      <ul class="contact-list">
        <li>
          <svg viewBox="0 0 24 24" aria-hidden="true"><path d="M6.6 10.8a15.1 15.1 0 0 0 6.6 6.6l2.2-2.2a1 1 0 0 1 1-.25 11.4 11.4 0 0 0 3.6.6 1 1 0 0 1 1 1V20a1 1 0 0 1-1 1A17 17 0 0 1 3 4a1 1 0 0 1 1-1h3.5a1 1 0 0 1 1 1c0 1.25.2 2.45.6 3.6a1 1 0 0 1-.25 1z"/></svg>
          555.014.2290
        </li>
        <li>
          <svg viewBox="0 0 24 24" aria-hidden="true"><path d="M2 5h20v2l-10 6L2 7zM2 9l10 6 10-6v10H2z"/></svg>
          info@mrtproperty.com
        </li>
        <li>
          <svg viewBox="0 0 24 24" aria-hidden="true"><path d="M12 2a10 10 0 1 0 0 20 10 10 0 0 0 0-20zm-1 17.9A8 8 0 0 1 4.1 11H7c0 3 1.5 6.5 4 8.9zM7 9H4.4A8 8 0 0 1 11 4.1C9 6 7.6 7.5 7 9zm6 10.9c2.5-2.4 4-5.9 4-8.9h2.9a8 8 0 0 1-6.9 8.9zM17 9c-.6-1.5-2-3-4-4.9A8 8 0 0 1 19.6 9z"/></svg>
          www.mrtproperty.com
        </li>
      </ul>
    </div>
  </section>

  <section class="card card--back" aria-label="Business card back">
    <div class="back-pattern" role="img" aria-label="Repeating brand symbol pattern fading from blue to navy"></div>
    <p class="brand-name brand-name--back">MRT Property</p>
  </section>
</body>
</html>
```